Website for my photography business

I need a website for my photography business, Bram Kellet Photography. I need a website that has a landing page with a cover photo of each kind of photography I do. For example, Nature, Weddings, Portraits and Architecture. I want it so that when someone comes onto my website they have to choose which kind of photography page they want to visit. So if they click on the wedding photo it will open to a page with my wedding portfolio images and a contact me button. If they choose nature photography I want them to be redirected to an e-commerce section where they can purchase prints. Architecture and Portraits should open up to their respective portfolios with about me and contact info. I like this kind of format because I want people who come to my website for a specific type of photography to be able to be directed there easily without having to look at a mix of other kinds of photography. I will provide a few files to use as placeholders. I have already purchased the bramkelletphotography.example domain name. A Wix website would be great because I am most familiar with it but I am open to anything.

Industry/Entity Type

Photographer

Number of Pages Required

5+ page

Requirements
Must have
• Landing Page and e-commerce

```html
<!DOCTYPE html>
<html lang="en">
<head>
<meta charset="utf-8">
<title>Bram Kellet Photography — Portraits</title>
<link href="https://fonts.googleapis.com/css2?family=Dancing+Script:wght@400;500&family=Lora:ital@1&family=Montserrat:wght@800&family=Mulish:wght@300;400;600&display=swap" rel="stylesheet">
<style>
:root{
  --ink:#1c1c1c;
  --muted:#a9a9a9;
  --rule:#c9c9c9;
  --paper:#ffffff;
  --mint:#4bd19e;
}
*{box-sizing:border-box;margin:0;padding:0}
html,body{width:885px;height:1200px;overflow:hidden;background:var(--paper)}
.page{position:relative;width:885px;height:1200px;color:var(--ink)}

.masthead{position:absolute;left:174px;top:32px;width:539px;height:104px;border:1.3px solid var(--ink);text-align:center}
.brand{font-family:"Dancing Script",cursive;font-weight:400;font-size:31px;line-height:1;margin-top:5px;letter-spacing:.2px}
.tagline{font-family:"Dancing Script",cursive;font-size:13.5px;line-height:1;margin-top:4px;color:#333}
.main-nav{display:flex;justify-content:center;margin-top:12px}
.main-nav a{font-family:"Lora",serif;font-style:italic;font-size:10.5px;color:var(--ink);text-decoration:none;padding:3px 10px;border-left:1px solid var(--rule);line-height:16px}
.main-nav a:first-child{border-left:none}
.main-nav a.current{color:var(--muted)}

.portfolio{position:absolute;left:258px;top:178px;display:grid;grid-template-columns:repeat(3,117px);grid-auto-rows:113px;gap:10px}
.tile{display:block}

.about{position:absolute;left:0;top:628px;width:885px;height:420px;display:flex}
.about-photo{width:443px;height:100%;background:linear-gradient(120deg,#5d6a73 0%,#2b2f36 45%,#1d2229 70%,#6e6256 100%)}
.about-panel{flex:1;background:var(--mint);text-align:center;padding-top:127px}
.about-title{font-family:"Montserrat",sans-serif;font-weight:800;font-size:29px;letter-spacing:13px;color:#fff;line-height:1;padding-left:13px}
.about-title span{color:#0c0c0c}
.about-text{font-family:"Mulish",sans-serif;font-weight:300;font-size:10.2px;line-height:15px;color:#113326;width:200px;margin:32px auto 0}

.contact-link{position:absolute;left:0;width:885px;top:1093px;text-align:center;font-family:"Mulish",sans-serif;font-weight:600;font-size:8.5px;letter-spacing:.6px;color:var(--ink)}
.contact-link svg{vertical-align:-1px;margin-right:3px}
.copyright{position:absolute;left:0;width:885px;top:1153px;text-align:center;font-family:"Lora",serif;font-style:italic;font-size:8px;color:#555}
.social{position:absolute;left:0;width:885px;top:1178px;display:flex;justify-content:center;gap:14px}
.social a{display:flex;align-items:center;gap:3px;font-family:"Mulish",sans-serif;font-weight:600;font-size:8px;color:var(--ink);text-decoration:none;line-height:10px}
.social a::before{content:"";width:6px;height:6px;border-radius:50%;background:var(--ink)}
</style>
</head>
<body>
<div class="page">
  <header class="masthead">
    <h1 class="brand">Bram Kellet Photography</h1>
    <p class="tagline">Creating extraordinary images that last infinetly</p>
    <nav class="main-nav">
      <a href="#">Home</a>
      <a href="#">Architecture</a>
      <a href="#" class="current">Portraits</a>
      <a href="#">Weddings</a>
      <a href="#">Nature</a>
      <a href="#">Contact me</a>
    </nav>
  </header>

  <section class="portfolio">
    <div class="tile" role="img" aria-label="Portrait of a smiling little girl held by her mother" style="background:linear-gradient(135deg,#8a7a66,#b9a8a6 55%,#7b8a9b)"></div>
    <div class="tile" role="img" aria-label="Studio portrait of a bearded man in glasses and a dark suit" style="background:linear-gradient(160deg,#2a2a2a,#111 60%,#3a3330)"></div>
    <div class="tile" role="img" aria-label="Black and white portrait of a smiling man" style="background:linear-gradient(160deg,#b9b9b9,#6e6e6e 60%,#9a9a9a)"></div>
    <div class="tile" role="img" aria-label="Grey dog against a coral backdrop" style="background:linear-gradient(160deg,#fb8a73,#f27f6b 40%,#4a4c52 75%,#f38570)"></div>
    <div class="tile" role="img" aria-label="Portrait of a curly-haired woman against a blue wall" style="background:linear-gradient(160deg,#8ec3e6,#7fb2d6 40%,#7a5139 65%,#a6dcd6)"></div>
    <div class="tile" role="img" aria-label="White fluffy dog against a pale blue backdrop" style="background:linear-gradient(160deg,#a9cde3,#e9eef0 55%,#9cc2da)"></div>
    <div class="tile" role="img" aria-label="Portrait of a young boy in a striped shirt" style="background:linear-gradient(120deg,#6a4a36,#c29a80 40%,#b9c7b2 75%,#d7ddd6)"></div>
    <div class="tile" role="img" aria-label="Family of four standing in a green field" style="background:linear-gradient(180deg,#e0e4e6 0%,#c7cfcf 38%,#5f8c3e 55%,#4f7a34 100%)"></div>
    <div class="tile" role="img" aria-label="Close family portrait of parents with two children" style="background:linear-gradient(150deg,#5c5648,#8f7a6b 45%,#6d7686)"></div>
  </section>

  <section class="about">
    <div class="about-photo" role="img" aria-label="Portrait of a bearded man in a dark leather jacket"></div>
    <div class="about-panel">
      <h2 class="about-title">ABOUT<span>ME</span></h2>
      <p class="about-text">I’m a paragraph. Double click here or click Edit Text to add some text of your own or to change the font. Tell your visitors a bit about your services.</p>
    </div>
  </section>

  <a class="contact-link">
    <svg width="10" height="7" viewBox="0 0 10 7" fill="none" stroke="#1c1c1c" stroke-width="0.9"><rect x="0.5" y="0.5" width="9" height="6"/><path d="M0.5 0.5 5 4 9.5 0.5"/></svg>Contact me!
  </a>
  <p class="copyright">© 2020 by Bram Kellet.</p>
  <nav class="social" aria-label="Social links">
    <a href="#">Profile</a>
    <a href="#">Updates</a>
    <a href="#">Gallery</a>
  </nav>
</div>
</body>
</html>
```